Vibrant, yet professional, stationery set and other designs required.

I need to source a fantastic designer for a new project as part of my company using a new logo designed via sketch harbor.

**UPDATE** I am not looking for just 'fine' design that will suffice. I am looking for something great.

We are a life assurance brokerage based in Dublin, Ireland and BrightRoost.ie is our new website aimed at providing services for young families in Ireland. We are hoping to be the 'Velro' level of service providers in this area and I am looking for the quality of design to reflect this :-) Hopefully that makes sense!

I have a preference for straight lines over curves and waves.

I need...

1. Business card
2. Letterhead
3. Banner (for printing - 76cm X 305cm)
4. Car branding for KORVA 9 (2014 sport model) I believe the templates are freely available online.

Target Market(s)

Parents in Ireland - Aged 27 to 50.

Industry/Entity Type

Financial Planning

Colors

Designer to choose colors to be used in the design.

Requirements
Must have
• All of the items listed in the description above. I like clean, bright, legible, vibrant and professional design.
Should not have
• No silly or 'cheap' looking designs. This is a professional company looking to provide a professional service.

```html
<!DOCTYPE html>
<html lang="en">
<head>
<meta charset="utf-8">
<title>BrightRoost.ie – Business Card</title>
<link href="https://fonts.googleapis.com/css2?family=Roboto:wght@400;500;700&display=swap" rel="stylesheet">
<style>
  :root {
    --page-bg: #ebebe9;
    --card-white: #fbfbfa;
    --card-slate: #7f9098;
    --ink-slate: #6b7a83;
    --ink-soft: #8a969d;
    --ink-white: #ffffff;
    --card-shadow: 0 6px 18px rgba(0,0,0,0.12);
  }
  html, body {
    margin: 0;
    padding: 0;
    width: 966px;
    height: 1200px;
    overflow: hidden;
    background: var(--page-bg);
    font-family: "Roboto", Arial, sans-serif;
  }
  .canvas {
    position: relative;
    width: 966px;
    height: 1200px;
  }
  .card {
    position: absolute;
    left: 203px;
    width: 560px;
    height: 350px;
    box-shadow: var(--card-shadow);
    box-sizing: border-box;
  }
  .card--front {
    top: 140px;
    background: var(--card-white);
    padding: 44px 44px 36px 44px;
  }
  .card--back {
    top: 710px;
    background: var(--card-slate);
    display: flex;
    align-items: center;
    justify-content: center;
  }
  .wordmark {
    margin: 0;
    font-weight: 700;
    font-size: 46px;
    letter-spacing: -0.5px;
    line-height: 1;
    color: var(--ink-slate);
  }
  .card--back .wordmark {
    font-size: 62px;
    color: var(--ink-white);
  }
  .address {
    margin: 46px 0 10px;
    font-size: 12.5px;
    line-height: 1.45;
    color: var(--ink-soft);
    font-style: normal;
  }
  .contact-list {
    list-style: none;
    margin: 0;
    padding: 0;
    font-size: 12.5px;
    line-height: 1.5;
    color: var(--ink-soft);
  }
  .contact-list li {
    display: flex;
    align-items: center;
    gap: 8px;
  }
  .contact-list svg {
    width: 11px;
    height: 11px;
    fill: var(--ink-slate);
    flex: none;
  }
  .person {
    position: absolute;
    right: 44px;
    top: 175px;
    text-align: right;
  }
  .person__name {
    margin: 0;
    font-size: 19px;
    font-weight: 500;
    color: var(--ink-slate);
    letter-spacing: 0.3px;
  }
  .person__role {
    margin: 4px 0 0;
    font-size: 12px;
    color: var(--ink-soft);
    letter-spacing: 0.3px;
  }
</style>
</head>
<body>
<main class="canvas">

  <section class="card card--front" aria-label="Business card front">
    <p class="wordmark">BrightRoost.ie</p>

    <address class="address">
      2140 Larchwood Row<br>
      Dunmore, Leinster 20517
    </address>

    <ul class="contact-list">
      <li>
        <svg viewBox="0 0 16 16" aria-hidden="true"><path d="M3.6 1.2l2.3 2.6-1.3 2a9 9 0 0 0 5.6 5.6l2-1.3 2.6 2.3-1.4 2.4C7.5 14.6 1.4 8.5 1.2 2.6z"/></svg>
        614 382 2907
      </li>
      <li>
        <svg viewBox="0 0 16 16" aria-hidden="true"><path d="M4.5 0h7A1.5 1.5 0 0 1 13 1.5v13a1.5 1.5 0 0 1-1.5 1.5h-7A1.5 1.5 0 0 1 3 14.5v-13A1.5 1.5 0 0 1 4.5 0zM5 2v10h6V2zm3 11a1 1 0 1 0 0 2 1 1 0 0 0 0-2z"/></svg>
        857 219 4630
      </li>
      <li>
        <svg viewBox="0 0 16 16" aria-hidden="true"><path d="M4 0h8v5H4zM1 6h14v8H1zm2 2v2h10V8z"/></svg>
        473 105 8826
      </li>
      <li>
        <svg viewBox="0 0 16 16" aria-hidden="true"><path d="M0 3h16v10H0zm1.5 1.5L8 9l6.5-4.5V4h-13z"/></svg>
        aidan@brightroost.com
      </li>
      <li>
        <svg viewBox="0 0 16 16" aria-hidden="true"><circle cx="8" cy="8" r="7.5"/></svg>
        www.brightroost.com
      </li>
    </ul>

    <div class="person">
      <p class="person__name">AIDAN HALE</p>
      <p class="person__role">CEO/FOUNDER</p>
    </div>
  </section>

  <section class="card card--back" aria-label="Business card back">
    <p class="wordmark">BrightRoost.ie</p>
  </section>

</main>
</body>
</html>
```